RTavenor Business Cards & Letterhead

I have a logo but need a design for some new business cards. We are a Design-Build Firm that specializes in the design and construction of commercial projects.
the cards need to be professional. no cartoon stuff.
i would like to have the cards in AI format so I can update the card as needed. Logo is provided.
Our Address is: 4187 Marlowe Ct. Apex, North Carolina 27614

```html
<!DOCTYPE html>
<html lang="en">
<head>
<meta charset="utf-8">
<title>RTavenor Business Card</title>
<link rel="stylesheet" href="https://fonts.googleapis.com/css2?family=Open+Sans:wght@400;600;700;800&display=swap">
<style>
  :root {
    --bg: #2b2e33;
    --card: #ffffff;
    --ink: #222222;
    --brand-grey: #555659;
    --brand-blue: #1a6fb5;
    --blue-dark: #0d3f6e;
    --blue-mid: #1466a8;
    --rule-grey: #9a9b9e;
  }
  * { box-sizing: border-box; margin: 0; padding: 0; }
  html, body { width: 1200px; height: 780px; overflow: hidden; }
  body {
    background: var(--bg);
    font-family: "Open Sans", Arial, sans-serif;
    position: relative;
  }
  .card {
    position: absolute;
    top: 240px;
    width: 520px;
    height: 300px;
    background: var(--card);
    border-radius: 16px;
    overflow: hidden;
    box-shadow: 0 10px 30px rgba(0,0,0,.35);
  }
  .card--front { left: 50px; }
  .card--back { left: 630px; }

  .swoosh { position: absolute; inset: 0; width: 100%; height: 100%; }

  .wordmark {
    display: flex;
    align-items: center;
    gap: 8px;
    font-weight: 800;
    color: var(--brand-grey);
    letter-spacing: -0.5px;
    text-transform: uppercase;
  }
  .wordmark__square { background: var(--brand-blue); display: block; }

  .card--front .wordmark { position: absolute; left: 30px; top: 22px; font-size: 28px; }
  .card--front .wordmark__square { width: 18px; height: 18px; }

  .contact {
    position: absolute;
    left: 62px;
    top: 78px;
    font-size: 11.5px;
    line-height: 16px;
    color: var(--ink);
  }
  .contact__address { margin-bottom: 4px; }
  .contact__list { list-style: none; }
  .contact__list li { display: flex; align-items: center; gap: 6px; }
  .contact__icon { width: 10px; height: 10px; flex: none; }

  .person {
    position: absolute;
    right: 34px;
    top: 118px;
    text-align: right;
  }
  .person__name {
    font-size: 19px;
    font-weight: 700;
    color: var(--brand-blue);
    text-transform: uppercase;
    letter-spacing: .3px;
  }
  .person__title { font-size: 12.5px; color: var(--ink); }
  .edge-tab {
    position: absolute;
    right: 0;
    top: 118px;
    width: 18px;
    height: 40px;
    background: linear-gradient(180deg, var(--blue-mid), var(--blue-dark));
  }

  .card--back { display: flex; align-items: center; justify-content: center; }
  .card--back .wordmark { font-size: 48px; gap: 12px; }
  .card--back .wordmark__square { width: 30px; height: 30px; }
</style>
</head>
<body>

<section class="card card--front" aria-label="Business card front">
  <svg class="swoosh" viewBox="0 0 520 300" preserveAspectRatio="none" aria-hidden="true">
    <defs>
      <linearGradient id="blueBand" x1="0" y1="0" x2="1" y2="1">
        <stop offset="0" stop-color="#1a74bb"/>
        <stop offset="1" stop-color="#0d3f6e"/>
      </linearGradient>
    </defs>
    <path d="M0,112 C10,200 90,232 220,232 C350,232 440,214 520,196 L520,300 L0,300 Z" fill="url(#blueBand)"/>
    <path d="M10,108 C22,188 100,220 222,222 C350,224 440,206 520,188" fill="none" stroke="var(--rule-grey)" stroke-width="5"/>
  </svg>

  <div class="wordmark"><span class="wordmark__square"></span>RTavenor</div>

  <div class="contact">
    <p class="contact__address">4187 Marlowe Ct. Apex,<br>North Carolina 27614</p>
    <ul class="contact__list">
      <li>
        <svg class="contact__icon" viewBox="0 0 10 10"><path d="M2 1 L4 3 L3 4 C4 6 5 7 6 7 L7 6 L9 8 L8 9.5 C4 9.5 0.5 6 0.5 2 Z" fill="var(--brand-blue)"/></svg>
        (919) 555-0148
      </li>
      <li>
        <svg class="contact__icon" viewBox="0 0 10 10"><circle cx="5" cy="5" r="4.5" fill="var(--brand-blue)"/><path d="M0.5 5 H9.5 M5 0.5 C2.5 3 2.5 7 5 9.5 M5 0.5 C7.5 3 7.5 7 5 9.5" stroke="#fff" stroke-width=".8" fill="none"/></svg>
        www.rtavenor.com
      </li>
      <li>
        <svg class="contact__icon" viewBox="0 0 10 10"><rect x="0.5" y="2" width="9" height="6.5" rx="1" fill="var(--brand-blue)"/><path d="M0.8 2.5 L5 5.8 L9.2 2.5" stroke="#fff" stroke-width=".8" fill="none"/></svg>
        RMT@RTavenor.com
      </li>
    </ul>
  </div>

  <div class="person">
    <p class="person__name">Ronan Tavenor</p>
    <p class="person__title">Founder/President</p>
  </div>
  <span class="edge-tab"></span>
</section>

<section class="card card--back" aria-label="Business card back">
  <div class="wordmark"><span class="wordmark__square"></span>RTavenor</div>
</section>

</body>
</html>
```